Harborview Estates Business Card for Apartment Buildings

Create business cards for resident managers who run apartment buildings. The audience is the public who are searching for apartment rentals, and current residents who live at the apartment building. Key design element will be incorporating the company logo, however, the logo cannot dominate. The building name and manager name are more important than the logo. Current business card design leaves little room for copy, so we may need to reduce the size on the current card to allow for more space for copy.

Target Market(s)

Adults 18-65 years of age, who are looking for an apartment rental, plus current residents who live at our apartment buildings.

Industry/Entity Type

Property Management

Contact Information for Business Card

A major design element will be use of the company logo. Important property and manager contact information must be part of the design. The size of the logo will need to be reduced to make room for building and manager contact copy.

Font styles to use
Sans Serif

Colors
3176b5
000000
959595
ffffff

Requirements
Must have
• 1) Incorporate the company logo.
• 2) Use the company colors (dark blue, black/grey, over white).
• 3) FEATURE THE BUILDING NAME
• 4) FEATURE THE MANAGER NAME
• 5) The company name is less important than BUILDING and MANAGER
• 6) Manager contact information
• **SEE ATTACHED CREATIVE BRIEF**
Nice to have
• 1) Back of card logo watermark
• 2) Ability to write notes on back of carfd
Should not have
• Avoid letting the company logo dominate the card, the building name and manager are more important than the company logo.

```html
<!DOCTYPE html>
<html lang="en">
<head>
<meta charset="utf-8">
<title>Harborview Estates Business Card</title>
<link href="https://fonts.googleapis.com/css2?family=Montserrat:wght@600;700&family=Roboto:wght@400;500&display=swap" rel="stylesheet">
<style>
  :root {
    --brand-blue: #3176b5;
    --band-dark: #1a5690;
    --band-light: #1b8ad4;
    --ink: #2b2b2b;
    --grey: #959595;
    --paper: #ffffff;
    --backdrop: #e6e6e6;
  }
  * { margin: 0; padding: 0; box-sizing: border-box; }
  html, body { width: 1200px; height: 726px; overflow: hidden; background: var(--backdrop); }
  .canvas { position: relative; width: 1200px; height: 726px; }

  .card {
    position: absolute;
    width: 540px; height: 309px;
    background: var(--paper);
    box-shadow: 0 8px 24px rgba(0,0,0,.12);
    overflow: hidden;
  }
  .card--back { left: 40px; top: 209px; }
  .card--front { left: 620px; top: 209px; }

  .brand {
    display: flex; align-items: center; gap: 8px;
    font-family: "Montserrat", sans-serif; font-weight: 700;
    color: var(--brand-blue); letter-spacing: .04em; text-transform: uppercase;
    white-space: nowrap;
  }
  .brand__mark { width: 11px; height: 11px; background: var(--brand-blue); flex: none; }

  .card--back .brand { position: absolute; left: 0; right: 0; top: 120px; justify-content: center; font-size: 20px; }
  .card--back .web {
    position: absolute; left: 0; right: 0; bottom: 44px; text-align: center;
    font-family: "Roboto", sans-serif; font-size: 14px; color: var(--ink);
  }
  .web__domain { color: var(--brand-blue); }

  .card--front .brand { position: absolute; left: 30px; top: 78px; font-size: 14px; }

  .name-band {
    position: absolute; left: 0; top: 112px; width: 440px; height: 74px;
    background: linear-gradient(90deg, var(--band-dark) 0%, var(--band-dark) 45%, var(--band-light) 100%);
    padding: 9px 0 0 30px;
  }
  .accent-band {
    position: absolute; left: 440px; right: 0; top: 88px; height: 40px;
    background: var(--band-light);
  }
  .name-band__name {
    font-family: "Montserrat", sans-serif; font-weight: 700;
    font-size: 31px; color: var(--paper); line-height: 1.1;
  }
  .name-band__title {
    font-family: "Roboto", sans-serif; font-size: 15px; color: var(--paper); opacity: .9; margin-top: 4px;
  }

  .contacts {
    position: absolute; left: 30px; top: 204px; list-style: none;
    font-family: "Roboto", sans-serif; font-size: 13px; color: var(--ink);
  }
  .contacts li { display: flex; align-items: center; gap: 10px; height: 22px; }
  .contacts svg { width: 13px; height: 13px; flex: none; }
</style>
</head>
<body>
<div class="canvas">

  <section class="card card--back" aria-label="Card back">
    <div class="brand"><span class="brand__mark"></span>Harborview Estates LLC</div>
    <p class="web">www.<span class="web__domain">harborviewestates</span>.us</p>
  </section>

  <section class="card card--front" aria-label="Card front">
    <div class="brand"><span class="brand__mark"></span>Harborview Estates LLC</div>

    <div class="accent-band"></div>
    <div class="name-band">
      <p class="name-band__name">Daniel Reyes</p>
      <p class="name-band__title">Property Manager</p>
    </div>

    <ul class="contacts">
      <li>
        <svg viewBox="0 0 16 16" fill="none" stroke="#1a5690" stroke-width="1.5"><circle cx="8" cy="8" r="6.5"/><path d="M5.5 5c0 3 2.5 5.5 5.5 5.5l.5-1.5-1.5-1-1 .8A4 4 0 0 1 7.2 7l.8-1-1-1.5z" fill="#1a5690" stroke="none"/></svg>
        555-201-4830
      </li>
      <li>
        <svg viewBox="0 0 16 16" fill="#1a5690"><rect x="4" y="1.5" width="8" height="4"/><rect x="1.5" y="6" width="13" height="6" rx="1"/><rect x="4" y="10" width="8" height="4.5" fill="#fff" stroke="#1a5690"/></svg>
        555-201-4831
      </li>
      <li>
        <svg viewBox="0 0 16 16" fill="none" stroke="#1a5690" stroke-width="1.4"><rect x="1.5" y="3.5" width="13" height="9"/><path d="M1.5 3.5 8 9l6.5-5.5"/></svg>
        daniel@harborviewestates.us
      </li>
      <li>
        <svg viewBox="0 0 16 16" fill="none" stroke="#1a5690" stroke-width="1.3"><circle cx="8" cy="8" r="6.5"/><ellipse cx="8" cy="8" rx="3" ry="6.5"/><path d="M1.5 8h13M2.5 5h11M2.5 11h11"/></svg>
        <span>www.<span class="web__domain">harborviewestates</span>.us</span>
      </li>
    </ul>
  </section>

</div>
</body>
</html>
```